R7M Horizon Business Card Design

We need a business card created for our New Business "R7M Horizon"<br/><br/>The business card design is up to you however the following information must be on the business card:<br/><br/>Front of the business card -<br/>Email :darrenp@r7mhorizon.nz<br/>Mobile: +64 (0) 22 4870 619<br/>Website: www.r7mhorizon.nz<br/>Card Owner Name: Darren Paltrow<br/>Company Title: Business Development Manager<br/>Slogan: "The BEST of both worlds". <br/>Logo On the front attached to the design brief<br/><br/>On the back: <br/>Space on the back for 4 more versions of the logo across the bottom of the card indicating different subsidiary brands - R7M Coffee, R7M Arts, R7M ?? (The card will be used for all of these brands - We Will add the extra subsidiary logos to the design once the design is finished (We are a graphics design team). <br/><br/>Other than that we want a premium feeling logo that remains universally usable depending on the business entity that we are using the card for. The use of bright bold colours would be great but we still want the card to feel premium.
Target Market(s)
Gift Design and Manufacturing Companies
Contact Information for Business Card
Front of the business card -
Email :darrenp@r7mhorizon.nz
Mobile: +64 (0) 22 4870 619
Website: www.r7mhorizon.nz
Card Owner Name: Darren Paltrow
Company Title: Business Development Manager
Slogan: "The BEST of both worlds".
Logo On the front attached to the design brief

```html
<!DOCTYPE html>
<html lang="en">
<head>
<meta charset="utf-8">
<title>R7M Horizon Business Card</title>
<link rel="stylesheet" href="https://fonts.googleapis.com/css2?family=Montserrat:wght@400;700&family=Open+Sans:wght@400;700&display=swap">
<style>
  :root {
    --brand-blue: #3541a0;
    --paper-white: #ffffff;
    --curve-grey: #a9a9a9;
    --backdrop: #2a2a2c;
    --ink-light: #ffffff;
    --slot-line: rgba(255,255,255,0.45);
  }
  * { box-sizing: border-box; margin: 0; padding: 0; }
  html, body {
    width: 1200px; height: 900px; overflow: hidden;
    background: var(--backdrop);
  }
  .stage { position: relative; width: 1200px; height: 900px; }
  .card {
    position: absolute; width: 640px; height: 370px;
    border-radius: 22px; overflow: hidden;
    box-shadow: 0 10px 28px rgba(0,0,0,0.45);
  }
  .card--front { left: 90px; top: 45px; background: var(--brand-blue); }
  .card--back  { left: 470px; top: 480px; background: var(--brand-blue); }

  .front-shape { position: absolute; inset: 0; width: 640px; height: 370px; }

  .brand-name {
    font-family: "Montserrat", sans-serif; font-weight: 700;
    letter-spacing: 0.5px; white-space: nowrap;
  }
  .brand-lockup { position: absolute; left: 48px; top: 170px; }
  .card--front .brand-name { font-size: 38px; color: var(--brand-blue); }
  .slogan {
    font-family: "Montserrat", sans-serif; font-weight: 400;
    font-size: 14px; color: var(--brand-blue); margin-top: 6px; padding-left: 2px;
  }

  .card--back .brand-name {
    position: absolute; left: 0; right: 0; top: 110px;
    text-align: center; font-size: 54px; color: var(--ink-light);
  }
  .subsidiary-row {
    position: absolute; left: 0; right: 0; bottom: 40px;
    display: flex; justify-content: center; gap: 36px; list-style: none;
  }
  .subsidiary-slot {
    width: 96px; height: 56px; border: 1.5px solid var(--slot-line); border-radius: 6px;
  }

  .contact-block {
    position: absolute; right: 36px; top: 36px; width: 300px;
    text-align: right; color: var(--ink-light);
    font-family: "Open Sans", sans-serif;
  }
  .owner-name { font-weight: 700; font-size: 21px; letter-spacing: 0.5px; text-transform: uppercase; }
  .owner-title { font-size: 14px; margin-top: 2px; }
  .contact-list { list-style: none; margin-top: 40px; }
  .contact-list li {
    display: flex; justify-content: flex-end; align-items: center; gap: 10px;
    font-size: 14px; line-height: 25px;
  }
  .contact-list svg { width: 14px; height: 14px; flex: none; }
  .address { margin-top: 22px; }
  .address li { align-items: flex-start; line-height: 20px; }
  .address svg { margin-top: 3px; }
</style>
</head>
<body>
<main class="stage">

  <section class="card card--front" aria-label="Business card front">
    <svg class="front-shape" viewBox="0 0 640 370" aria-hidden="true">
      <circle cx="60" cy="345" r="384" fill="var(--curve-grey)"/>
      <circle cx="40" cy="330" r="380" fill="var(--paper-white)"/>
    </svg>
    <div class="brand-lockup">
      <div class="brand-name">R7M Horizon</div>
      <p class="slogan">The BEST of both worlds</p>
    </div>

    <div class="contact-block">
      <p class="owner-name">Darren Paltrow</p>
      <p class="owner-title">Business Development Manager</p>
      <ul class="contact-list">
        <li>+64 (0) 22 4870 619
          <svg viewBox="0 0 16 16"><circle cx="8" cy="8" r="7" fill="none" stroke="#fff" stroke-width="1.2"/><path d="M5.5 4.5l1.5 0 .6 1.8-.9.8a5 5 0 0 0 2.2 2.2l.8-.9 1.8.6v1.5c-3.5.3-6.3-2.5-6-6z" fill="#fff"/></svg>
        </li>
        <li>darrenp@r7mhorizon.nz
          <svg viewBox="0 0 16 16"><rect x="1.5" y="4" width="13" height="8.5" rx="1" fill="#fff"/><path d="M1.8 4.5L8 9l6.2-4.5" fill="none" stroke="var(--brand-blue)" stroke-width="1.2"/></svg>
        </li>
        <li>www.r7mhorizon.nz
          <svg viewBox="0 0 16 16" fill="none" stroke="#fff" stroke-width="1.1"><circle cx="8" cy="8" r="6.5"/><ellipse cx="8" cy="8" rx="2.8" ry="6.5"/><path d="M1.5 8h13M2.5 5h11M2.5 11h11"/></svg>
        </li>
      </ul>
      <ul class="contact-list address">
        <li>Street Name, City Name,<br>zip code - 00000
          <svg viewBox="0 0 16 16"><path d="M8 1a5 5 0 0 0-5 5c0 3.5 5 9 5 9s5-5.5 5-9a5 5 0 0 0-5-5z" fill="#fff"/><circle cx="8" cy="6" r="1.8" fill="var(--brand-blue)"/></svg>
        </li>
      </ul>
    </div>
  </section>

  <section class="card card--back" aria-label="Business card back">
    <div class="brand-name">R7M Horizon</div>
    <ul class="subsidiary-row" aria-label="Space for subsidiary brand marks">
      <li class="subsidiary-slot"></li>
      <li class="subsidiary-slot"></li>
      <li class="subsidiary-slot"></li>
      <li class="subsidiary-slot"></li>
    </ul>
  </section>

</main>
</body>
</html>
```